Create a capturing book cover for The Hollow Lantern

Book Title: The Hollow Lantern
Subtitle: Rising Past the Restless Tide
Author: Leshonda Marbury

Synopsis of book:
She didn’t really know what she wanted to do, but she knew she wanted to be successful. She struggled with identifying with what she was passionate about and what her purpose was for her life. Fear, turmoil, relationships, and career paths created turbulence in her long journey to fulfill her vision and lifetime goals. The Hollow Lantern exemplifies women who struggle with these things. The Hollow Lantern digs into the crevices of a blurry vision, disturbed, and fearful woman.

-The book focuses on a woman who is not necessarily physically cripple, but mentally, spiritually, and emotionally crippled.

The photos attached are just examples (not all have to be used)

Target Market(s)

Women who are dealing with barriers that are holding them back from reaching their goals or being successful

Font styles to use
Serif
Sans Serif

Colors
6b449b
b7a5cd

Requirements
Must have
• purple incorporated (not the full cover)
• I would like an African American woman, dominican woman, or mixed (you cannot tell what ethnicity she is) on the front cover if any.
Nice to have
• I would like the cover to tell the story. My ideas were maybe an actual crippled woman looking into the mirror at a woman who is at peace, or two women in one that shows one struggling and one living in happiness, or a crippled woman with her back turned and a path with something that symbolizes happiness at the end, or a lady sitting on the floor kind of distraught. I really want the designer to be creative. I do not have an exact image of what I want it to look like. These are just ideas. They do not have to be within the realms that I mentioned.
Should not have
• Extravagant text
• cartoon or animated pictures
• do not want a dark cover

```html
<!DOCTYPE html>
<html lang="en">
<head>
<meta charset="utf-8">
<title>The Hollow Lantern — Full Cover</title>
<link rel="stylesheet" href="https://fonts.googleapis.com/css2?family=Cinzel:wght@400;500;600&family=Marcellus&family=Cormorant+Garamond:wght@400&family=Tinos&display=swap">
<style>
  :root {
    --plum-deep: #2c1240;
    --plum: #4a1f66;
    --violet: #6b449b;
    --lilac: #b7a5cd;
    --blush: #f6e4e8;
    --ink: #24122f;
    --paper: #ffffff;
    --back-text: #f3eef6;
  }
  * { margin: 0; padding: 0; box-sizing: border-box; }
  html, body { width: 1200px; height: 928px; overflow: hidden; background: #ffffff; }
  .cover { position: relative; width: 1200px; height: 928px; overflow: hidden; }

  /* Back cover */
  .back {
    position: absolute; left: 0; top: 0; width: 557px; height: 928px;
    background: radial-gradient(ellipse at 45% 10%, #5a2a78 0%, var(--plum) 45%, #34144a 100%);
    color: var(--back-text);
  }
  .back-title { position: absolute; left: 0; width: 570px; top: 58px; text-align: center; font-family: "Cinzel", serif; font-weight: 400; color: #f4e9f1; }
  .back-title .the { display: block; font-size: 20px; letter-spacing: 3px; line-height: 24px; }
  .back-title .main { display: block; font-size: 46px; letter-spacing: 5px; line-height: 50px; }
  .back-title .second { display: block; font-size: 46px; letter-spacing: 12px; line-height: 46px; }
  .back-rule { position: absolute; left: 140px; top: 176px; width: 290px; height: 2px; background: linear-gradient(90deg, transparent, #e8d6e8, transparent); }
  .back-subtitle { position: absolute; left: 0; width: 580px; top: 182px; text-align: center; font-family: "Cinzel", serif; font-size: 21px; line-height: 26px; color: #f1e6f0; }
  .blurb { position: absolute; left: 72px; top: 266px; width: 440px; font-family: "Tinos", serif; font-size: 17.4px; line-height: 23px; text-align: justify; text-align-last: center; color: var(--back-text); }
  .blurb p + p { margin-top: 23px; }
  .code-area { position: absolute; left: 323px; top: 750px; width: 225px; height: 135px; background: var(--paper); }

  /* Spine */
  .spine {
    position: absolute; left: 557px; top: 0; width: 68px; height: 928px;
    background: linear-gradient(180deg, #4c1f68 0%, #3e175a 60%, #361450 100%);
  }
  .spine-title, .spine-author {
    position: absolute; left: 34px; writing-mode: vertical-rl; transform: translateX(-50%);
    white-space: nowrap; color: #e8cfe6;
  }
  .spine-title { top: 40px; font-family: "Cormorant Garamond", serif; font-size: 38px; letter-spacing: 5px; text-transform: uppercase; }
  .spine-author { top: 655px; font-family: "Tinos", serif; font-size: 26px; letter-spacing: 2px; }

  /* Front cover */
  .front { position: absolute; left: 625px; top: 0; width: 575px; height: 928px; }
  .front-art { position: absolute; inset: 0; width: 575px; height: 928px; }
  .front-title { position: absolute; left: 0; width: 575px; top: 52px; text-align: center; font-family: "Cinzel", serif; font-weight: 400; color: var(--ink); }
  .front-title .the { display: block; font-size: 30px; letter-spacing: 5px; line-height: 34px; }
  .front-title .main { display: block; font-size: 82px; letter-spacing: 6px; line-height: 84px; }
  .front-title .second { display: block; font-size: 72px; letter-spacing: 14px; line-height: 72px; }
  .front-rule { position: absolute; left: 52px; top: 235px; width: 456px; height: 4px; background: linear-gradient(90deg, rgba(60,30,80,0.2), #2a1638 20%, #2a1638 80%, rgba(60,30,80,0.2)); border-radius: 2px; }
  .front-subtitle { position: absolute; left: 0; width: 575px; top: 248px; text-align: center; font-family: "Cinzel", serif; font-weight: 600; font-size: 21px; line-height: 26px; color: var(--ink); }
  .front-author { position: absolute; left: 0; width: 575px; top: 858px; text-align: center; font-family: "Marcellus", serif; font-size: 31px; letter-spacing: 7px; color: #f7f1f5; }
</style>
</head>
<body>
<main class="cover">
  <section class="back">
    <h2 class="back-title">
      <span class="the">The</span>
      <span class="main">Hollow</span>
      <span class="second">Lantern</span>
    </h2>
    <div class="back-rule"></div>
    <p class="back-subtitle">Rising Past<br>the Restless Tide</p>
    <div class="blurb">
      <p>She did not know exactly what she wanted to do, but she knew she wanted to succeed. Finding her passion felt out of reach, and her purpose stayed hidden behind a blurry vision of the life she hoped to build. Fear, turmoil, strained relationships and shifting career paths stirred up a storm around her, and every step of her long journey toward her goals seemed to meet another wave. She was not broken in body, yet she was worn down in mind, spirit and heart, carrying a light that had grown dim inside her. This is the story of that quiet struggle and of the slow, brave work of rising again.</p>
      <p>The Hollow Lantern speaks to every woman held back by unseen barriers. It digs into the crevices of doubt and fear, and it shows how a wounded heart can find peace, rediscover purpose and step boldly toward the success it was always meant to reach.</p>
    </div>
    <div class="code-area"></div>
  </section>

  <section class="spine">
    <span class="spine-title">The Hollow Lantern</span>
    <span class="spine-author">Leshonda Marbury</span>
  </section>

  <section class="front">
    <svg class="front-art" viewBox="0 0 575 928" role="img" aria-label="Photograph: a woman seen from behind sitting on a hilltop at sunset, gazing over a hazy city toward the light, with a white dove landing on a rock beside her as a sign of hope">
      <defs>
        <linearGradient id="sky" x1="0" y1="0" x2="0" y2="1">
          <stop offset="0" stop-color="#fbf2f3"/>
          <stop offset="0.26" stop-color="#f3e0e4"/>
          <stop offset="0.34" stop-color="#e2c6cf"/>
          <stop offset="0.39" stop-color="#d9bcc6"/>
          <stop offset="0.43" stop-color="#a98497"/>
          <stop offset="0.5" stop-color="#8a6479"/>
          <stop offset="0.62" stop-color="#5e3d66"/>
          <stop offset="0.8" stop-color="#432656"/>
          <stop offset="1" stop-color="#301a42"/>
        </linearGradient>
        <radialGradient id="sun" cx="0.95" cy="0.3" r="0.5">
          <stop offset="0" stop-color="#ffffff" stop-opacity="0.95"/>
          <stop offset="0.5" stop-color="#fbe8e6" stop-opacity="0.35"/>
          <stop offset="1" stop-color="#ffffff" stop-opacity="0"/>
        </radialGradient>
        <radialGradient id="warm" cx="0.55" cy="0.52" r="0.4">
          <stop offset="0" stop-color="#c79483" stop-opacity="0.45"/>
          <stop offset="1" stop-color="#c79483" stop-opacity="0"/>
        </radialGradient>
        <radialGradient id="shade" cx="0.34" cy="0.78" r="0.32">
          <stop offset="0" stop-color="#24132f" stop-opacity="0.75"/>
          <stop offset="1" stop-color="#24132f" stop-opacity="0"/>
        </radialGradient>
        <radialGradient id="light" cx="0.88" cy="0.84" r="0.13">
          <stop offset="0" stop-color="#efe6f1" stop-opacity="0.7"/>
          <stop offset="1" stop-color="#efe6f1" stop-opacity="0"/>
        </radialGradient>
      </defs>
      <rect width="575" height="928" fill="url(#sky)"/>
      <rect width="575" height="928" fill="url(#sun)"/>
      <rect width="575" height="928" fill="url(#warm)"/>
      <rect width="575" height="928" fill="url(#shade)"/>
      <rect width="575" height="928" fill="url(#light)"/>
    </svg>
    <h1 class="front-title">
      <span class="the">The</span>
      <span class="main">Hollow</span>
      <span class="second">Lantern</span>
    </h1>
    <div class="front-rule"></div>
    <p class="front-subtitle">Rising Past<br>the Restless Tide</p>
    <p class="front-author">Leshonda Marbury</p>
  </section>
</main>
</body>
</html>
```